Cosmetic oil label design

We need a label for a cosmetic oganic Argan Oil. The oil is organic imported from Morocco, cold pressed without any preservatives. The lable is for our round 30ml Airless Bottle with clear body Matte Gold Cap, Shiny Gold Collar. We want to communicate that our product is organic natural and works for all beauty needs. We want the emphasis on the words No preservatives, additives or perfumes
We have attached a picture of the bottle and our compnay's logo.

the bottle demensions are Width/Front: 33.0mm
Length/Depth: 33.0mm
Height: 115.0mm
Lable demensions: Lenght 4inch, width 1.75inch.

let us know if you need any other information, cheers!
Updates

Target Market(s)

Our target customer is mainly women 16-70, and also men or anyone looking to have healthy skin and hair using natural products

Industry/Entity Type

Product

Requirements
Must have
• Front side must have:
- attached logo
-words: Authentic Moroccan Argan Oil, No preservatives, additives or perfumes,
L’Huile d’Argan, Produit du Maroc, Imported from Morocco, 30ml

Back side
-Ingredients: 100% Pure Argania Spinosa (Argan Oil)
-Directions: Message into skin, hair or desired area until completely absorbed
-Manufactured for and distributed by Velora Traders
482 W 97th street New York , NY 10027
Nice to have
• Would be nice if we can fit the following information in the back of the label

Rich in vitamin E and essential fatty acids,Argan oil has several benefits. It Hydrates and nourishes skin and hair. Can be used for treating dry skin, split ends softening cuticles. It works for all types of skin.

```html
<!DOCTYPE html>
<html lang="en">
<head>
<meta charset="utf-8">
<title>Argan Oil Label – Back</title>
<link rel="stylesheet" href="https://fonts.googleapis.com/css2?family=Questrial&family=Didact+Gothic&display=swap">
<style>
  :root {
    --gold-deep: #2a1e0e;
    --gold-dark: #6b4a18;
    --gold-mid: #b0822f;
    --gold-light: #d6a746;
    --gold-glow: #e3b654;
    --oval: #2b211a;
    --oval-text: #e6c47a;
    --ink: #1c150e;
    --ink-soft: #3e3020;
    --ornament: #2b211a;
  }
  * { margin: 0; padding: 0; box-sizing: border-box; }
  html, body { width: 1200px; height: 2740px; overflow: hidden; background: #000; }
  .label {
    position: relative;
    width: 1200px;
    height: 2740px;
    overflow: hidden;
    background:
      radial-gradient(ellipse 900px 700px at 600px 2250px, rgba(233,188,90,0.55), rgba(233,188,90,0) 70%),
      radial-gradient(ellipse 700px 900px at 0px 0px, rgba(20,14,6,0.85), rgba(20,14,6,0) 70%),
      radial-gradient(ellipse 700px 900px at 1200px 0px, rgba(20,14,6,0.85), rgba(20,14,6,0) 70%),
      linear-gradient(180deg, var(--gold-deep) 0%, var(--gold-dark) 22%, var(--gold-mid) 45%, var(--gold-light) 70%, var(--gold-glow) 82%, var(--gold-mid) 100%);
    font-family: "Questrial", "Didact Gothic", sans-serif;
  }
  .benefits-oval {
    position: absolute;
    left: 0; top: 0;
    width: 1200px; height: 1200px;
  }
  .ornament {
    position: absolute;
    top: 1030px;
    width: 120px;
    height: 90px;
  }
  .ornament--left { left: 160px; }
  .ornament--right { left: 920px; }
  .benefits {
    position: absolute;
    left: 0; width: 1200px;
    top: 60px;
    text-align: center;
    color: var(--oval-text);
    font-size: 60px;
    line-height: 68px;
  }
  .benefits strong { font-weight: 700; font-family: "Didact Gothic", sans-serif; -webkit-text-stroke: 1px var(--oval-text); }
  .info {
    position: absolute;
    left: 0; width: 1200px;
    text-align: center;
    color: var(--ink);
    font-size: 58px;
    line-height: 72px;
  }
  .info h2 {
    font-weight: 400;
    font-size: 62px;
    -webkit-text-stroke: 1.2px var(--ink);
  }
  .ingredients { top: 1580px; }
  .directions { top: 1840px; }
  .distributor {
    position: absolute;
    left: 0; width: 1200px;
    top: 2270px;
    text-align: center;
    color: var(--ink-soft);
    font-size: 54px;
    line-height: 72px;
  }
</style>
</head>
<body>
<main class="label">
  <svg class="benefits-oval" viewBox="0 0 1200 1200" aria-hidden="true">
    <ellipse cx="600" cy="560" rx="350" ry="592" fill="var(--oval)"/>
  </svg>
  <svg class="ornament ornament--left" viewBox="0 0 120 90" role="img" aria-label="Leaf flourish ornament">
    <rect x="0" y="0" width="120" height="90" rx="40" fill="var(--ornament)"/>
  </svg>
  <svg class="ornament ornament--right" viewBox="0 0 120 90" role="img" aria-label="Leaf flourish ornament">
    <rect x="0" y="0" width="120" height="90" rx="40" fill="var(--ornament)"/>
  </svg>

  <section class="benefits">
    <p>Rich in<br><strong>vitamin E</strong><br>and essential<br>fatty acids,<br>Argan oil has<br>several benefits.<br>It hydrates &amp; nourishes<br>skin &amp; hair, Can<br>be used for treating<br>dry skin, split ends<br>softening cuticles.<br>It works for<br>all types<br>of skin</p>
  </section>

  <section class="info ingredients">
    <h2>Ingredients</h2>
    <p>100% Pure Argania Spinosa<br>(Argan Oil)</p>
  </section>

  <section class="info directions">
    <h2>Directions</h2>
    <p>Message into<br>skin, hair or desired area until<br>completely absorbed.</p>
  </section>

  <footer class="distributor">
    <p>Manufactured for and distributed<br>by Velora Traders 482 W 97th<br>street New York , NY 10027</p>
  </footer>
</main>
</body>
</html>
```